Business Cards - Brightpath Horizon

need to design unique business card for my mortgage business. I need to design credit card style business card for my business or any unique idea that you might have

Target Market(s)

Home Loan customers

Industry/Entity Type

Mortgage Brokerage

Contact Information for Business Card

please design credit card style or very unique style business card

Colors

Designer to choose colors to be used in the design.

Requirements
Must have
• Name
• position
• Phone number
• fax number
• email address
• website address
• social media address
• All above fields will be provided once design in finalised

```html
<!DOCTYPE html>
<html lang="en">
<head>
<meta charset="utf-8">
<title>Brightpath Horizon – Business Card</title>
<link rel="stylesheet" href="https://fonts.googleapis.com/css2?family=Oswald:wght@600&family=Work+Sans:wght@400;500&family=Cormorant+Garamond:wght@600&display=swap">
<style>
  :root {
    --backdrop: #161616;
    --card: #262626;
    --card-edge: #2e2e2e;
    --brand-blue: #1f5fc4;
    --logo-blue: #3a4fb8;
    --accent-orange: #f08a1c;
    --text-light: #f2f2f2;
  }
  * { box-sizing: border-box; margin: 0; padding: 0; }
  html, body {
    width: 1200px; height: 900px; overflow: hidden;
    background: radial-gradient(ellipse at 60% 40%, #2a2a2a 0%, var(--backdrop) 75%);
    font-family: "Work Sans", Arial, sans-serif;
  }
  .card-stack {
    position: absolute; left: 270px; top: 50px;
    display: flex; flex-direction: column; gap: 40px;
  }
  .card {
    position: relative; width: 660px; height: 380px;
    background: linear-gradient(135deg, var(--card) 0%, var(--card-edge) 100%);
    box-shadow: 0 14px 30px rgba(0,0,0,.55);
  }
  /* front */
  .brand-lockup {
    position: absolute; inset: 0;
    display: flex; align-items: center; justify-content: center; gap: 16px;
  }
  .brand-mark { width: 34px; height: 34px; border-radius: 50%; background: var(--accent-orange); }
  .brand-name {
    font-family: "Cormorant Garamond", Georgia, serif; font-weight: 600;
    font-size: 46px; letter-spacing: 2px; color: var(--logo-blue);
    text-transform: uppercase;
  }
  /* back */
  .identity {
    position: absolute; left: 60px; top: 138px; width: 240px; text-align: right;
  }
  .person-name {
    font-family: "Oswald", "Arial Narrow", sans-serif; font-weight: 600;
    font-size: 38px; line-height: 1; color: var(--brand-blue); text-transform: uppercase;
  }
  .person-role {
    margin-top: 8px; font-size: 18px; letter-spacing: 1px; color: var(--text-light);
  }
  .divider {
    position: absolute; left: 322px; top: 132px; width: 2px; height: 84px;
    background: var(--accent-orange);
  }
  .contact-list {
    position: absolute; left: 344px; top: 128px; list-style: none;
  }
  .contact-list li {
    display: flex; align-items: center; gap: 12px;
    font-size: 17px; line-height: 23px; color: var(--text-light);
  }
  .contact-list svg { width: 14px; height: 14px; fill: var(--brand-blue); flex: none; }
  .location {
    position: absolute; left: 60px; top: 300px; font-size: 18px; color: var(--text-light);
  }
  .location-label { color: var(--accent-orange); font-weight: 500; }
</style>
</head>
<body>
  <main class="card-stack">
    <section class="card card-front">
      <div class="brand-lockup">
        <span class="brand-mark"></span>
        <span class="brand-name">Brightpath Horizon</span>
      </div>
    </section>

    <section class="card card-back">
      <div class="identity">
        <h1 class="person-name">Daniel Reyes</h1>
        <p class="person-role">FOUNDER</p>
      </div>
      <div class="divider"></div>
      <ul class="contact-list">
        <li><svg viewBox="0 0 14 14" aria-hidden="true"><path d="M4 0h6a1 1 0 0 1 1 1v12a1 1 0 0 1-1 1H4a1 1 0 0 1-1-1V1a1 1 0 0 1 1-1zm0 2v9h6V2z"/></svg>(555) 014-2287</li>
        <li><svg viewBox="0 0 14 14" aria-hidden="true"><path d="M3 0h8v4H3zM1 5h12a1 1 0 0 1 1 1v5h-3v3H3v-3H0V6a1 1 0 0 1 1-1zm3 5v3h6v-3z"/></svg>(555) 014-3390</li>
        <li><svg viewBox="0 0 14 14" aria-hidden="true"><path d="M0 2h14v10H0zm1 1.2V4l6 4 6-4v-.8z"/></svg>d.reyes@brightpathmail.net</li>
        <li><svg viewBox="0 0 14 14" aria-hidden="true"><path d="M7 0a7 7 0 1 0 0 14A7 7 0 0 0 7 0zm0 1.5c.9 1.2 1.4 2.6 1.6 4.5H5.4C5.6 4.1 6.1 2.7 7 1.5zM5.4 8h3.2c-.2 1.9-.7 3.3-1.6 4.5-.9-1.2-1.4-2.6-1.6-4.5z"/></svg>brightpathhorizon.com</li>
      </ul>
      <p class="location"><span class="location-label">Location:</span> 48 Lakeview Rd, Springvale ON K7A 2C3</p>
    </section>
  </main>
</body>
</html>
```